Business Card Design

The Kestrel Lodge Inn is the most centrally located motel in Grafton.
We are the only family owned motel in Grafton.
Our colour scheme is blue, whiteand black.

I have uploaded a photo of our new rooms and the logo for you to use Thanks. Looking good

Industry/Entity Type

Motel

Contact Information for Business Card

The Kestrel Lodge Inn
Gareth & Lorna Pelling
Owner/Operators
14-16 Wexbury Lane, Grafton NSW 2460
Ph: 02 6617 3904
Email: thekestrellodgeinn@mailvista.example
reception@kestrellodgeinn.example.au
www.kestrellodgeinn.example.au

Colors
0392cd
0455a3

```html
<!DOCTYPE html>
<html lang="en">
<head>
<meta charset="utf-8">
<title>The Kestrel Lodge Inn – Business Card</title>
<link rel="stylesheet" href="https://fonts.googleapis.com/css2?family=Exo+2:wght@400;500;600&display=swap">
<style>
  :root {
    --bg: #c9cbce;
    --card: #ffffff;
    --blue-light: #86bdec;
    --blue-dark: #063f98;
    --blue-text: #0455a3;
    --ink: #1d1d1f;
    --grey: #5a5a5e;
    --notch-shadow: #b4b8bf;
  }
  * { margin: 0; padding: 0; box-sizing: border-box; }
  html, body { width: 1200px; height: 895px; overflow: hidden; }
  body {
    background: var(--bg);
    font-family: "Exo 2", sans-serif;
    color: var(--ink);
    position: relative;
  }
  .card {
    position: absolute;
    width: 700px;
    height: 400px;
    left: 250px;
    background: var(--card);
    box-shadow: 0 6px 18px rgba(0,0,0,.22);
    overflow: hidden;
  }
  .card--front { top: 32px; }
  .card--back { top: 463px; }
  .card-graphics { position: absolute; inset: 0; }

  .brand {
    position: absolute;
    display: flex;
    align-items: center;
    gap: 14px;
  }
  .brand-dot {
    width: 34px; height: 34px;
    border-radius: 50%;
    background: var(--blue-text);
    flex: none;
  }
  .brand-name {
    font-weight: 600;
    color: var(--blue-text);
    letter-spacing: .5px;
    white-space: nowrap;
  }
  .card--front .brand { left: 34px; top: 44px; }
  .card--front .brand-name { font-size: 30px; }
  .card--back .brand { left: 0; right: 0; top: 168px; justify-content: center; }
  .card--back .brand-name { font-size: 34px; }
  .card--back .brand-dot { width: 40px; height: 40px; }

  .person { position: absolute; left: 440px; top: 100px; }
  .person-name {
    font-size: 17px; font-weight: 500;
    color: var(--blue-text); letter-spacing: 1.2px;
    white-space: nowrap;
  }
  .person-role {
    font-size: 10px; color: var(--grey);
    letter-spacing: 1px; margin-top: 6px;
  }

  .contact {
    position: absolute;
    line-height: 1.5;
    color: var(--ink);
    white-space: nowrap;
  }
  .contact--web { left: 18px; top: 206px; font-size: 11.5px; letter-spacing: .1px; }
  .contact--address { left: 262px; top: 222px; font-size: 14px; letter-spacing: .5px; }
  .contact--phone { left: 490px; top: 256px; font-size: 16px; letter-spacing: .6px; }
</style>
</head>
<body>

<section class="card card--front" aria-label="Business card front">
  <svg class="card-graphics" viewBox="0 0 700 400" aria-hidden="true">
    <polygon fill="var(--blue-light)" points="0,150 216,150 232,170 216,190 0,190"/>
    <polygon fill="var(--notch-shadow)" points="216,150 222,150 238,170 222,190 216,190 232,170"/>
    <polygon fill="var(--blue-light)" points="226,162 452,162 468,182 452,202 226,202 242,182"/>
    <polygon fill="var(--notch-shadow)" points="452,162 458,162 474,182 458,202 452,202 468,182"/>
    <polygon fill="var(--blue-light)" points="462,196 700,196 700,236 462,236 478,216"/>
    <polygon fill="var(--blue-dark)" points="0,344 700,344 700,400 0,400"/>

    <g class="icon-globe" fill="none" stroke="#fff" stroke-width="1.6">
      <circle cx="108" cy="170" r="11"/>
      <ellipse cx="108" cy="170" rx="5" ry="11"/>
      <line x1="97" y1="170" x2="119" y2="170"/>
      <line x1="99" y1="164" x2="117" y2="164"/>
      <line x1="99" y1="176" x2="117" y2="176"/>
    </g>
    <path class="icon-pin" fill="#fff" d="M344 171a8 8 0 0 1 16 0c0 6-8 14-8 14s-8-8-8-14z"/>
    <circle cx="352" cy="171" r="3" fill="var(--blue-light)"/>
    <g class="icon-phone" fill="none" stroke="#fff" stroke-width="1.6">
      <rect x="582" y="203" width="14" height="25" rx="2"/>
      <line x1="586" y1="224" x2="592" y2="224"/>
    </g>
  </svg>

  <div class="brand">
    <span class="brand-dot"></span>
    <span class="brand-name">The Kestrel Lodge Inn</span>
  </div>

  <div class="person">
    <p class="person-name">GARETH &amp; LORNA PELLING</p>
    <p class="person-role">OWNER/OPERATORS</p>
  </div>

  <div class="contact contact--web">
    <p>thekestrellodgeinn@mailvista.example</p>
    <p>reception@kestrellodgeinn.example.au</p>
    <p>www.kestrellodgeinn.example.au</p>
  </div>
  <div class="contact contact--address">
    <p>14-16 Wexbury Lane</p>
    <p>Grafton NSW 2460</p>
  </div>
  <div class="contact contact--phone">
    <p>Ph: 02 6617 3904</p>
  </div>
</section>

<section class="card card--back" aria-label="Business card back">
  <svg class="card-graphics" viewBox="0 0 700 400" aria-hidden="true">
    <polygon fill="var(--blue-light)" points="0,0 230,0 230,44 0,44"/>
    <polygon fill="var(--blue-light)" points="240,0 470,0 470,44 240,44"/>
    <polygon fill="var(--blue-light)" points="480,0 700,0 700,44 480,44"/>
    <polygon fill="var(--notch-shadow)" points="228,0 236,0 248,22 236,44 228,44 240,22"/>
    <polygon fill="#fff" points="230,0 240,0 252,22 240,44 230,44 242,22"/>
    <polygon fill="var(--notch-shadow)" points="468,0 476,0 488,22 476,44 468,44 480,22"/>
    <polygon fill="#fff" points="470,0 480,0 492,22 480,44 470,44 482,22"/>

    <polygon fill="var(--blue-dark)" points="0,336 700,336 700,400 0,400"/>
    <polygon fill="var(--notch-shadow)" points="228,336 236,336 248,368 236,400 228,400 240,368"/>
    <polygon fill="#fff" points="230,336 240,336 252,368 240,400 230,400 242,368"/>
    <polygon fill="var(--notch-shadow)" points="468,336 476,336 488,368 476,400 468,400 480,368"/>
    <polygon fill="#fff" points="470,336 480,336 492,368 480,400 470,400 482,368"/>
  </svg>

  <div class="brand">
    <span class="brand-dot"></span>
    <span class="brand-name">The Kestrel Lodge Inn</span>
  </div>
</section>

</body>
</html>
```